ORLA - Óptica Médica - web design and concept

Website concept - Create and develop our website design and structure. ORLA is an optical store chain, and we are looking to establish our web and digital concept. In attachment there are several pictures about our stores and our logo.

The website structure should be user friendly. Colors should be light and the design as simple and minimalist as possible. There are different variations of the logothat can be used, check the file.

The website will include optical collections and sun collections as an online store. Also, a medical menu should be considered in order for clients to schedule optometry appointments. There should also be a menu for client assistance where the clients can read about glass maintenance in our workshop.
Updates

Low design quality

Number of Pages Required

5+ page

Font styles to use
Serif
Sans Serif

Requirements
Must have
• Must be user-friendly and minimalist.
• Please USE PICTURES FROM THE BRANDS we sell: MERUN, BOSKA, PNW, KOLE, BAMPE
Nice to have
• Nice to inspire: ZEK glasses (see website https://ch.shopzek.com/en/)
• Nice to inspire: https://merun-eyewear.com/
• Nice to ispire: https://www.pnwglobe.com/en/
Should not have
• Hysteric colors and shapes

```html
<!DOCTYPE html>
<html lang="en">
<head>
<meta charset="utf-8">
<title>ORLA – The Voyager</title>
<link href="https://fonts.googleapis.com/css2?family=Raleway:wght@400;500;600;700&display=swap" rel="stylesheet">
<style>
:root{
  --ink:#111111;
  --text:#333333;
  --muted:#777777;
  --line:#e2e2e2;
  --panel:#f7f7f7;
  --photo:#f3f3f3;
  --price:#d8262a;
  --dark:#252525;
  --white:#ffffff;
}
*{box-sizing:border-box;margin:0;padding:0}
html,body{width:1200px;height:2586px;overflow:hidden;background:var(--white)}
body{position:relative;font-family:"Raleway",sans-serif;color:var(--text)}
h1,h2,h3,h4{font-weight:400}
.abs{position:absolute}

/* header */
.phone{left:121px;top:76px;font-size:14px;display:flex;align-items:center;gap:10px;color:var(--ink)}
.brand{left:500px;width:200px;top:58px;text-align:center;color:var(--ink)}
.brand-mark{display:block;font-family:"Raleway",sans-serif;font-weight:500;font-size:34px;letter-spacing:8px;line-height:1}
.header-icons{left:952px;top:76px;display:flex;gap:22px;align-items:center}
.breadcrumb{left:121px;top:176px;font-size:16px;letter-spacing:.5px;color:var(--ink);display:flex;gap:22px}
.breadcrumb b{font-weight:600}

/* gallery */
.main-photo{left:121px;top:247px;width:446px;height:382px;background:radial-gradient(ellipse at center,#e9dfd6 0%,var(--photo) 60%)}
.thumbs{left:121px;top:638px;display:flex;gap:11px}
.thumbs span{width:104px;height:98px;background:linear-gradient(180deg,#f1ede9,#e6ddd4)}

/* details */
.details{left:631px;top:245px;width:460px;color:var(--ink)}
.title{font-size:19px;font-weight:600}
.subtitle{font-size:14px;margin-top:2px}
.price{font-size:20px;color:var(--price);margin-top:16px}
.h-small{font-size:18px;font-weight:500;margin-top:34px}
.lead{font-size:13.5px;line-height:17px;margin-top:4px;color:var(--text)}
.qty-row{display:flex;align-items:center;margin-top:28px}
.qty-row .lbl{font-size:19px;width:110px}
.qty{display:flex;border:1px solid var(--line);height:36px}
.qty span{width:30px;display:flex;align-items:center;justify-content:center;font-size:14px}
.qty span:nth-child(2){border-left:1px solid var(--line);border-right:1px solid var(--line)}
.cart-btn{margin-left:12px;background:var(--ink);color:var(--white);font-size:19px;font-weight:600;height:40px;width:185px;display:flex;align-items:center;justify-content:center}
.wish{font-size:14px;margin-top:14px;display:flex;gap:10px;align-items:center;padding-bottom:14px;border-bottom:1px solid var(--line);width:360px}
.avail{font-size:20px;margin-top:16px}
.meta{font-size:17px;margin-top:4px;display:flex;align-items:center;gap:14px}
.dots{display:flex;gap:9px}
.dots i{width:9px;height:9px;border-radius:50%}
.share{font-size:19px;margin-top:14px;display:flex;align-items:center;gap:12px}
.circle{width:34px;height:34px;border-radius:50%;background:var(--ink)}

/* more info */
.more{left:121px;top:796px;width:962px;height:197px;border:2px solid var(--line)}
.more h3{font-size:19px;font-weight:600;padding:16px 19px;border-bottom:2px solid var(--line);color:var(--ink)}
.more p{font-size:13.5px;line-height:17px;padding:16px 26px}

/* related */
.section-title{left:0;width:1200px;text-align:center;font-size:24px;font-weight:400;color:var(--ink);letter-spacing:.5px}
.related{left:117px;top:1143px;display:flex;gap:14px}
.card{width:232px;height:248px;border:1px solid #ececec;text-align:center}
.card-photo{height:150px;margin:8px;background:radial-gradient(ellipse at center,#cfcfcf 0%,var(--white) 70%)}
.card-photo.rose{background:radial-gradient(ellipse at center,#e7b7c8 0%,var(--white) 70%)}
.card-photo.teal{background:radial-gradient(ellipse at center,#a9c7be 0%,var(--white) 70%)}
.card h4{font-size:14px;font-weight:500;margin-top:10px;color:var(--ink)}
.card p{font-size:13px;margin-top:4px}

/* features */
.features{left:121px;top:1491px;display:flex;gap:20px}
.feature{width:307px;height:176px;background:var(--panel);text-align:center;padding-top:34px}
.feature h4{font-size:20px;font-weight:500;margin-top:12px;color:var(--ink)}
.feature p{font-size:13px;color:var(--muted);margin-top:4px}

/* newsletter */
.newsletter{left:0;top:1725px;width:1200px;text-align:center;color:var(--ink)}
.newsletter h2{font-size:26px;font-weight:500}
.newsletter p{font-size:15px;margin-top:4px}
.signup{left:324px;top:1810px;width:552px;height:36px;border:1px solid var(--line);border-radius:18px;display:flex;overflow:hidden}
.signup span{flex:1;font-size:14px;color:#999;padding:9px 22px}
.signup b{width:123px;background:var(--ink);color:var(--white);font-size:15px;display:flex;align-items:center;justify-content:center;border-radius:18px}

/* brands */
.brands{left:121px;top:1983px;display:flex;gap:14px}
.brand-tile{width:180px;height:120px;background:var(--panel);display:flex;align-items:center;justify-content:center;font-size:24px;font-weight:600;color:var(--ink);letter-spacing:1px}
.arrow{top:2029px}

/* footer */
.footer{left:0;top:2155px;width:1200px;height:431px;background:var(--dark);color:var(--white)}
.f-logo{left:121px;top:48px;width:115px;text-align:center}
.f-logo .brand-mark{font-size:26px;letter-spacing:5px}
.f-rule{height:3px;background:var(--white);width:115px;margin-top:18px}
.f-about{left:119px;top:142px;font-size:14px;line-height:21px;width:260px}
.f-about li{list-style:none;display:flex;align-items:center;gap:9px}
.pay{left:121px;top:274px;display:flex;gap:8px}
.pay span{width:42px;height:24px;border-radius:3px;background:#4a6fb3}
.pay span:nth-child(2){background:#eeeeee}
.pay span:nth-child(3){background:#8a2a6b}
.pay span:nth-child(4){background:#2b4aa0}
.pay span:nth-child(5){background:#e56a22}
.f-head{font-size:14px;font-weight:600}
.f-head::after{content:"";display:block;width:112px;height:3px;background:var(--white);margin-top:12px}
.f-info{left:412px;top:93px}
.f-info ul{margin-top:20px;list-style:none;font-size:13.5px;line-height:21px}
.f-info li::before{content:"";display:inline-block;width:7px;height:7px;border-radius:50%;background:var(--white);margin-right:14px}
.f-tags{left:600px;top:93px}
.tags{margin-top:18px;display:grid;grid-template-columns:repeat(3,auto);gap:10px 8px;justify-content:start}
.tags span{border:1px solid #bbb;font-size:13px;padding:2px 10px;text-align:center;min-width:56px}
.tags span.on{background:#000;border-color:#000}
.f-insta{left:846px;top:93px}
.insta{margin-top:20px;display:grid;grid-template-columns:repeat(3,75px);gap:5px}
.insta span{height:67px;background:linear-gradient(135deg,#d9c8bb,#8f8f8f)}
.f-bottom{left:0;top:2540px;width:1200px;border-top:1px solid #555}
.copy{left:119px;top:2554px;font-size:13.5px;color:var(--white)}
.socials{left:900px;top:2552px;display:flex;gap:13px}
.socials span{width:26px;height:26px;border-radius:50%;background:var(--white)}
</style>
</head>
<body>

<header>
  <div class="abs phone">
    <svg width="20" height="20" viewBox="0 0 24 24" fill="none" stroke="#111" stroke-width="1.8"><circle cx="12" cy="12" r="10"/><path d="M8.5 7.5l2 2-1.2 1.5c.8 1.6 2 2.8 3.6 3.6l1.5-1.2 2 2-1.4 1.3c-3.6-.4-6.9-3.7-7.3-7.3z"/></svg>
    123-456-7890
  </div>
  <div class="abs brand"><span class="brand-mark">ORLA</span></div>
  <div class="abs header-icons">
    <svg width="14" height="13" viewBox="0 0 24 22" fill="none" stroke="#111" stroke-width="2.5"><path d="M12 20S2 13.5 2 7.5A5 5 0 0 1 12 5a5 5 0 0 1 10 2.5C22 13.5 12 20 12 20z"/></svg>
    <svg width="15" height="14" viewBox="0 0 24 22" fill="none" stroke="#111" stroke-width="2.5"><path d="M1 2h4l3 12h12l3-9H7"/><circle cx="10" cy="19" r="1.6"/><circle cx="18" cy="19" r="1.6"/></svg>
    <svg width="13" height="13" viewBox="0 0 24 24" fill="none" stroke="#111" stroke-width="3"><circle cx="10" cy="10" r="7"/><path d="M15 15l7 7"/></svg>
    <svg width="16" height="13" viewBox="0 0 16 13" fill="#111"><rect width="16" height="2.6"/><rect y="5.2" width="16" height="2.6"/><rect y="10.4" width="16" height="2.6"/></svg>
  </div>
  <nav class="abs breadcrumb"><span>HOME</span><span>/</span><span>PRODUCTS</span><span>/</span><b>CHELSEA'S ROUND LENSES</b></nav>
</header>

<main>
  <div class="abs main-photo" role="img" aria-label="Round tortoiseshell eyeglasses with gold bridge"></div>
  <div class="abs thumbs">
    <span role="img" aria-label="Front view of the frames"></span>
    <span role="img" aria-label="Angled view of the frames"></span>
    <span role="img" aria-label="Close-up of the hinge"></span>
    <span role="img" aria-label="Side view of the temple"></span>
  </div>

  <section class="abs details">
    <h1 class="title">THE VOYAGER</h1>
    <div class="subtitle">(TITANIUM/ACETATE)</div>
    <div class="price">$ 699.99</div>
    <h2 class="h-small">INSPIRATION</h2>
    <p class="lead">Lorem Ipsum is simply dummy text of the printing and typesetting industry. Lorem Ipsum has been the industry's standard dummy text ever since the 1500s, when an unknown printer took a galley of type and scrambled it to make a type specimen book. It has survived not only five centuries,</p>
    <div class="qty-row">
      <span class="lbl">Quantity</span>
      <div class="qty"><span>-</span><span>1</span><span>+</span></div>
      <div class="cart-btn">+ ADD TO CART</div>
    </div>
    <div class="wish">
      <svg width="13" height="12" viewBox="0 0 24 22" fill="none" stroke="#111" stroke-width="2.5"><path d="M12 20S2 13.5 2 7.5A5 5 0 0 1 12 5a5 5 0 0 1 10 2.5C22 13.5 12 20 12 20z"/></svg>
      ADD TO WISHLISH
    </div>
    <div class="avail">AVAILABLE</div>
    <div class="meta">Product Code : 000000</div>
    <div class="meta">Color
      <span class="dots"><i style="background:#7a2a1a"></i><i style="background:#f2c200"></i><i style="background:#2aa12a"></i><i style="background:#999"></i></span>
    </div>
    <div class="share">SHARE : <span class="circle"></span><span class="circle"></span></div>
  </section>

  <section class="abs more">
    <h3>MORE INFO</h3>
    <p>Lorem Ipsum is simply dummy text of the printing and typesetting industry. Lorem Ipsum has been the industry's standard dummy text ever since the 1500s, when an unknown printer took a galley of type and scrambled it to make a type specimen book. It has survived not only five centuries,</p>
  </section>

  <h2 class="abs section-title" style="top:1056px">RELATED PRODUCT</h2>
  <div class="abs related">
    <div class="card"><div class="card-photo" role="img" aria-label="Black aviator sunglasses"></div><h4>Product Name</h4><p>30€</p></div>
    <div class="card"><div class="card-photo" role="img" aria-label="Black aviator sunglasses"></div><h4>Product Name</h4><p>30€</p></div>
    <div class="card"><div class="card-photo rose" role="img" aria-label="Round sunglasses with pink lenses"></div><h4>Product Name</h4><p>50€</p></div>
    <div class="card"><div class="card-photo teal" role="img" aria-label="Oversized sunglasses with gradient lenses"></div><h4>Product Name</h4><p>30€</p></div>
  </div>

  <div class="abs features">
    <div class="feature">
      <svg width="44" height="36" viewBox="0 0 44 36" fill="#999"><path d="M0 16L44 0 30 36 21 22z"/><path d="M21 22L44 0 17 31z" fill="#666"/></svg>
      <h4>Free Shipping</h4><p>Free For All Over order $ 200.00</p>
    </div>
    <div class="feature">
      <svg width="40" height="40" viewBox="0 0 40 40"><circle cx="20" cy="20" r="18" fill="none" stroke="#111" stroke-width="3" stroke-dasharray="4 2"/><circle cx="20" cy="20" r="12" fill="#111"/><path d="M20 12l2.4 5 5.4.6-4 3.7 1.1 5.3L20 24l-4.9 2.6 1.1-5.3-4-3.7 5.4-.6z" fill="#fff"/></svg>
      <h4>Money Come Back</h4><p>100% Money Back Guarantee</p>
    </div>
    <div class="feature">
      <svg width="40" height="40" viewBox="0 0 40 40" fill="none" stroke="#111" stroke-width="2.5"><circle cx="20" cy="20" r="17"/><path d="M20 10v10l6 5"/></svg>
      <h4>24/7 Support</h4><p>Services Support 24/7 Fast</p>
    </div>
  </div>

  <section class="abs newsletter">
    <h2>Subscribe To Our Newsletter</h2>
    <p>To Receive The latest News And Update</p>
  </section>
  <div class="abs signup"><span>Your E-Mail</span><b>SUBMIT</b></div>

  <h2 class="abs section-title" style="top:1920px">Brands</h2>
  <svg class="abs arrow" style="left:54px" width="26" height="26" viewBox="0 0 26 26" fill="none" stroke="#111" stroke-width="2"><circle cx="13" cy="13" r="11.5"/><path d="M15 8l-5 5 5 5"/></svg>
  <div class="abs brands">
    <div class="brand-tile">ROVANE</div>
    <div class="brand-tile">HELSOR</div>
    <div class="brand-tile" style="font-size:20px">MARLOW PIKE</div>
    <div class="brand-tile">SERAVEL</div>
    <div class="brand-tile">ONDI</div>
  </div>
  <svg class="abs arrow" style="left:1120px" width="26" height="26" viewBox="0 0 26 26" fill="none" stroke="#111" stroke-width="2"><circle cx="13" cy="13" r="11.5"/><path d="M11 8l5 5-5 5"/></svg>
</main>

<footer class="abs footer">
  <div class="abs f-logo"><span class="brand-mark">ORLA</span><div class="f-rule"></div></div>
  <ul class="abs f-about">
    <li>Lorem Ipsum is simply dummy text</li>
    <li>ipsum is simply the &nbsp;dummy... ›</li>
    <li>☎ Phone: 123 456 7890</li>
    <li>✉ Email:info@orla.com</li>
    <li>
      <svg width="11" height="14" viewBox="0 0 12 16" fill="#fff"><path d="M6 0a6 6 0 0 1 6 6c0 4-6 10-6 10S0 10 0 6a6 6 0 0 1 6-6zm0 3.5a2.5 2.5 0 1 0 0 5 2.5 2.5 0 0 0 0-5z"/></svg>
      Address : 12th Street, City .Usa</li>
  </ul>
  <div class="abs pay"><span></span><span></span><span></span><span></span><span></span></div>

  <div class="abs f-info">
    <div class="f-head">INFORMATION</div>
    <ul><li>Home</li><li>Woman</li><li>Men</li><li>Kids</li><li>Testimonials</li><li>Blogs</li><li>Contact us</li></ul>
  </div>
  <div class="abs f-tags">
    <div class="f-head">POPULAR TAGE</div>
    <div class="tags">
      <span>Kids</span><span>Men</span><span>Lady</span>
      <span>Woman</span><span>Latest</span><span>Specials</span>
      <span>Faishion</span><span>Eye</span><span>offers</span>
      <span class="on">Faishion</span><span>COOL</span>
    </div>
  </div>
  <div class="abs f-insta">
    <div class="f-head">INSTAGRAM</div>
    <div class="insta">
      <span role="img" aria-label="Customer wearing glasses"></span>
      <span role="img" aria-label="Customer wearing sunglasses"></span>
      <span role="img" aria-label="Customer wearing glasses"></span>
      <span role="img" aria-label="Customer wearing glasses"></span>
      <span role="img" aria-label="Customer wearing glasses"></span>
      <span role="img" aria-label="Customer wearing glasses"></span>
    </div>
  </div>
</footer>
<div class="abs f-bottom"></div>
<div class="abs copy">CopyRight ©2018 Orla. All Right Reserve</div>
<div class="abs socials"><span></span><span></span><span></span><span></span><span></span></div>

</body>
</html>
```